Luxury Wine Label for New Startup Winery

We need a wine label for our new winery startup. We have worked with a local designer but do not feel the resulting label / logo have the elevation required to present our brand as a luxury wine. Our winery is called "Quailbrook Vineyards" and we are focused on extremely high quality hand crafted artisan and estate wines from the Pacific Northwest.
We would like to see designs that utilize a tree line, or other imagery that represents the "Quailbrook" part of our company name. Another interesting feature could be wood grain.
A logo will be required based on your design so please design with this in mind:
This logo should be consistent with the wine bottle label design, and should be representative of our high end exclusive wine while giving a sense of place (Oregon/ Pacific Northwest.)
I will supply an image of the design we received from our local designer, PLEASE NOTE: in general we do like wood grain and tree line concepts but feel the execution was poorly done.
ATTN: Logo design should be suitable for use on: Bottles (Red wine/rose/white wine), Bussiness cards, vehicle signage, business signage, etc
P.S.:
If you have a design that is not outside the box we are still interested in seeing it.
Label is for a burgundy style bottle with a label height of 3.5 - 4" and a width of 3.5-4"
any label <= 4"x4" and >=3.5"x3.5" will be acceptable:
HOWEVER Width should be greater than or equal to height due to the bottle format
Target Market(s)
Wine enthusiasts with adequate discretionary budgets to afford $100 bottles of wine.
Industry/Entity Type
Wine / Winery
Requirements
Must have
- A sense of luxury, a feel of exclusivity, and a theme consistent with our product and brand name
Nice to have
- Tree line, wood grain or other wood themes. Serif fonts
Should not have
- anything cheesy, off topic, hard to read script fonts or anything that makes the label hard to read from a few feet away or too busy

```html
<!DOCTYPE html>
<html lang="en">
<head>
<meta charset="UTF-8">
<title>Quailbrook Vineyards – Syrah Label</title>
<link rel="stylesheet" href="https://fonts.googleapis.com/css2?family=Cinzel:wght@400;500;600&display=swap">
<style>
  :root {
    --backdrop: #ffffff;
    --ink-black: #050505;
    --silver-light: #f4f4f4;
    --silver-mid: #b9b9b9;
    --silver-dark: #5e5e5e;
    --moon-white: #ffffff;
    --label-white: #f7f5f0;
    --gold-light: #f5e27a;
    --gold-mid: #d9b43a;
    --gold-dark: #9c7a16;
    --wood-light: #8a6746;
    --wood-mid: #5f432b;
    --wood-dark: #3a2617;
    --cream: #efe6cf;
  }
  * { margin: 0; padding: 0; box-sizing: border-box; }
  html, body {
    width: 1200px;
    height: 1200px;
    overflow: hidden;
    background: var(--backdrop);
  }
  .canvas {
    position: relative;
    width: 1200px;
    height: 1200px;
  }
  .wine-label {
    position: absolute;
    left: 100px;
    top: 100px;
    width: 1000px;
    height: 1000px;
    overflow: hidden;
    background: var(--ink-black);
    box-shadow: 0 10px 30px rgba(0,0,0,0.25);
  }
  .treeline-scene {
    position: absolute;
    left: 0; top: 0;
    width: 1000px;
    height: 470px;
    background:
      radial-gradient(circle at 50% 105%, var(--moon-white) 0, var(--moon-white) 330px, rgba(255,255,255,0) 345px),
      linear-gradient(180deg, var(--silver-dark) 0%, var(--silver-light) 38%, var(--silver-mid) 62%, var(--silver-dark) 100%);
  }
  .treeline-scene::after {
    content: "";
    position: absolute;
    left: 0; right: 0; bottom: 0;
    height: 200px;
    background: linear-gradient(180deg, rgba(5,5,5,0) 0%, rgba(5,5,5,0.85) 70%, var(--ink-black) 100%);
  }
  .brand-block {
    position: absolute;
    left: 0; top: 470px;
    width: 1000px;
    height: 298px;
    background: var(--ink-black);
    color: var(--label-white);
    font-family: "Cinzel", "Times New Roman", serif;
    text-align: center;
  }
  .brand-name {
    position: absolute;
    left: 0; right: 0;
    top: 30px;
    font-size: 92px;
    font-weight: 500;
    letter-spacing: 0.02em;
    line-height: 1;
  }
  .brand-descriptor {
    position: absolute;
    left: 0; right: 0;
    top: 128px;
    font-size: 66px;
    font-weight: 400;
    letter-spacing: 0.12em;
    line-height: 1;
  }
  .region {
    position: absolute;
    left: 0; right: 0;
    top: 220px;
    display: flex;
    justify-content: center;
    align-items: center;
    gap: 22px;
    font-size: 28px;
    letter-spacing: 0.14em;
    line-height: 1;
  }
  .region-rule {
    width: 34px;
    height: 3px;
    background: var(--label-white);
  }
  .gold-rule {
    position: absolute;
    left: 0;
    width: 1000px;
    background: linear-gradient(180deg, var(--gold-light) 0%, var(--gold-mid) 55%, var(--gold-dark) 100%);
  }
  .gold-rule--top { top: 768px; height: 14px; }
  .wood-panel {
    position: absolute;
    left: 0; top: 782px;
    width: 1000px;
    height: 218px;
    background: linear-gradient(180deg, var(--wood-mid) 0%, var(--wood-light) 35%, var(--wood-mid) 65%, var(--wood-dark) 100%);
  }
  .varietal {
    position: absolute;
    left: 0; right: 0;
    top: 812px;
    text-align: center;
    font-family: "Cinzel", "Times New Roman", serif;
    font-size: 84px;
    font-weight: 500;
    letter-spacing: 0.12em;
    line-height: 1;
    color: var(--cream);
  }
  .vintage-band {
    position: absolute;
    left: 0; top: 912px;
    width: 1000px;
    height: 46px;
    display: flex;
    justify-content: center;
    align-items: center;
    background: linear-gradient(180deg, var(--gold-light) 0%, var(--gold-mid) 55%, var(--gold-dark) 100%);
    font-family: "Cinzel", "Times New Roman", serif;
    font-size: 24px;
    font-weight: 600;
    letter-spacing: 0.14em;
    color: var(--ink-black);
  }
</style>
</head>
<body>
  <main class="canvas">
    <article class="wine-label">
      <div class="treeline-scene" role="img" aria-label="Silhouetted evergreen tree line against a metallic silver sky with a large white moon"></div>

      <header class="brand-block">
        <h1 class="brand-name">QUAILBROOK</h1>
        <p class="brand-descriptor">VINEYARDS</p>
        <p class="region">
          <span class="region-rule"></span>
          <span>WILLAMETTE VALLEY</span>
          <span class="region-rule"></span>
        </p>
      </header>

      <div class="gold-rule gold-rule--top"></div>
      <div class="wood-panel" role="img" aria-label="Dark walnut wood grain texture"></div>
      <h2 class="varietal">SYRAH</h2>
      <p class="vintage-band">ESTATE | 2023 | GROWN</p>
    </article>
  </main>
</body>
</html>
```